Maple Roster Business Card for recruitment company

We are looking for a Business Card Design that incorporates our personal details and our busines name and logo. We are a specialized search consultancy that recruit Property and Construction professionals.
We would like a business card that stands out and is appealing to the Construction and Property industry as well.

Target Market(s)

people in the construction and property industry

Contact Information for Business Card

Business Name and logo

Font styles to use
Serif

Colors
0094D4
00A9DD
6FCCEA
C7EBF8
E9F6FB

Requirements
Must have
• Business name and logo as well as contact details
Should not have
• No photos of us please

```html
<!DOCTYPE html>
<html lang="en">
<head>
<meta charset="utf-8">
<title>Maple Roster – Business Card</title>
<link rel="stylesheet" href="https://fonts.googleapis.com/css2?family=Josefin+Sans:wght@400&family=Montserrat:wght@400;600&display=swap">
<style>
  :root {
    --stage: #2a2a2a;
    --teal-deep: #063d52;
    --teal-mid: #174f61;
    --brand-dark: #0c4a5f;
    --brand-light: #2bb3e0;
    --ink: #3d3d3d;
    --rule: #0c4a5f;
    --grey-band: #6b6b6b;
    --paper: #ffffff;
  }
  * { margin: 0; padding: 0; box-sizing: border-box; }
  html, body { width: 1200px; height: 900px; overflow: hidden; }
  body {
    background: var(--stage);
    font-family: "Montserrat", sans-serif;
    position: relative;
  }
  .card {
    position: absolute;
    left: 270px;
    width: 660px;
    height: 380px;
    overflow: hidden;
  }
  .card-front {
    top: 50px;
    background: linear-gradient(100deg, var(--teal-deep) 0%, var(--teal-mid) 100%);
    display: flex;
    align-items: center;
    justify-content: center;
  }
  .brand {
    display: flex;
    align-items: center;
    gap: 16px;
    font-family: "Josefin Sans", sans-serif;
    font-weight: 400;
  }
  .brand-mark {
    border-radius: 50%;
    flex: none;
  }
  .front-brand {
    font-size: 56px;
    letter-spacing: 3px;
    color: var(--brand-light);
  }
  .front-brand .brand-mark {
    width: 40px;
    height: 40px;
    background: var(--brand-light);
  }
  .card-back {
    top: 470px;
    background: var(--paper);
  }
  .back-art { position: absolute; inset: 0; }
  .back-brand {
    position: absolute;
    left: 40px;
    top: 30px;
    gap: 12px;
    font-size: 40px;
    letter-spacing: 2px;
    color: var(--brand-dark);
  }
  .back-brand .brand-mark {
    width: 28px;
    height: 28px;
    background: var(--brand-dark);
  }
  .person {
    position: absolute;
    right: 80px;
    top: 146px;
    text-align: right;
  }
  .person-name {
    font-weight: 600;
    font-size: 30px;
    line-height: 36px;
    color: var(--brand-dark);
    letter-spacing: 0.5px;
  }
  .person-role {
    margin-top: 2px;
    font-size: 18px;
    line-height: 24px;
    color: var(--ink);
    letter-spacing: 1px;
  }
  .contacts {
    position: absolute;
    left: 56px;
    top: 232px;
    list-style: none;
    font-size: 18px;
    color: var(--ink);
    line-height: 27px;
  }
  .contacts li { display: flex; align-items: center; gap: 8px; }
  .contacts svg { width: 14px; height: 14px; flex: none; }
  .location {
    position: absolute;
    left: 360px;
    top: 342px;
    display: flex;
    align-items: center;
    gap: 8px;
    color: var(--paper);
    font-size: 19px;
  }
  .location svg { width: 14px; height: 18px; }
</style>
</head>
<body>

<section class="card card-front">
  <div class="brand front-brand">
    <span class="brand-mark"></span>
    <span class="brand-name">MAPLE ROSTER</span>
  </div>
</section>

<section class="card card-back">
  <svg class="back-art" viewBox="0 0 660 380" aria-hidden="true">
    <line x1="60" y1="218" x2="582" y2="218" stroke="var(--rule)" stroke-width="1.5"/>
    <rect x="640" y="170" width="20" height="48" fill="var(--brand-dark)"/>
    <polygon points="0,352 320,352 300,380 0,380" fill="var(--grey-band)"/>
    <polygon points="330,322 660,322 660,380 296,380" fill="var(--brand-dark)"/>
  </svg>

  <div class="brand back-brand">
    <span class="brand-mark"></span>
    <span class="brand-name">MAPLE ROSTER</span>
  </div>

  <div class="person">
    <p class="person-name">DANIEL HARROW</p>
    <p class="person-role">FOUNDER</p>
  </div>

  <ul class="contacts">
    <li>
      <svg viewBox="0 0 14 14"><path d="M3 1l2.5 2.5L4 5.5c1 2 2.5 3.5 4.5 4.5l2-1.5L13 11l-1.5 2C6 13 1 8 1 2.5z" fill="var(--brand-dark)"/></svg>
      +64 27 480 2291
    </li>
    <li>
      <svg viewBox="0 0 14 14"><rect x="1" y="3" width="12" height="8" fill="none" stroke="var(--brand-dark)" stroke-width="1.4"/><path d="M1 3l6 5 6-5" fill="none" stroke="var(--brand-dark)" stroke-width="1.4"/></svg>
      hello@mapleroster.nz
    </li>
    <li>
      <svg viewBox="0 0 14 14"><circle cx="7" cy="7" r="6" fill="none" stroke="var(--brand-dark)" stroke-width="1.2"/><ellipse cx="7" cy="7" rx="2.5" ry="6" fill="none" stroke="var(--brand-dark)" stroke-width="1"/><line x1="1" y1="7" x2="13" y2="7" stroke="var(--brand-dark)" stroke-width="1"/></svg>
      www.mapleroster.nz
    </li>
  </ul>

  <div class="location">
    <svg viewBox="0 0 14 18"><path d="M7 0C3.1 0 0 3 0 6.8 0 11.8 7 18 7 18s7-6.2 7-11.2C14 3 10.9 0 7 0zm0 9.5a2.7 2.7 0 1 1 0-5.4 2.7 2.7 0 0 1 0 5.4z" fill="var(--paper)"/></svg>
    Kestrel Bay, New Zealand
  </div>
</section>

</body>
</html>
```